Business Card Re-Design/Update

We'd like to update out business cards. I've included our current "Style guide" which has the colour scheme of the organisation in it. I've also included the branding files with logos etc in them.

I've also included a copy of one of our existing cards so that you can see how ugly/dated they look. I'd like a fresh modern corporate look.

Target Market(s)

These are for our clients, potential clients, industry contacts - like all business cards

Contact Information for Business Card

Name
Position
Company Address - Level 1, 47 Fernby Street, Carlow Qld 4072
Direct Phone
mobile
Email
Website -www.korvalit.com.au
Logo

Colors

Designer to choose colors to be used in the design.

Requirements
Must have
• Main Logo
• Cards will need to be editable to be able to personalize them for each new employee.
Nice to have
• The MapOut, ShipWell, KeepSteady would be okay to have if they can be sensibly and professionally added to the look without detracting from the main imagery.
• Maybe they could go on the back of the card? will leave this to your creative discretion as to whether/where they fit.
Should not have
• Should not have decorative or script fonts

```html
<!DOCTYPE html>
<html lang="en">
<head>
<meta charset="utf-8">
<title>Korvalit Business Card</title>
<link rel="stylesheet" href="https://fonts.googleapis.com/css2?family=Roboto:wght@400;500;700&family=Roboto+Condensed:wght@400;700&display=swap">
<style>
  :root {
    --backdrop: #e8e8e8;
    --card: #f7f7f7;
    --red: #b01c22;
    --red-dark: #9c141b;
    --red-soft: #d9686c;
    --ink: #1f1f1f;
    --grey: #555555;
    --white: #ffffff;
  }
  * { margin: 0; padding: 0; box-sizing: border-box; }
  html, body { width: 1200px; height: 960px; overflow: hidden; }
  body {
    position: relative;
    background: var(--backdrop);
    font-family: "Roboto", Arial, sans-serif;
  }
  .card {
    position: absolute;
    width: 600px;
    height: 343px;
    background: var(--card);
    overflow: hidden;
    box-shadow: 0 2px 4px rgba(0,0,0,0.25);
  }
  .card-front { left: 314px; top: 113px; }
  .card-back { left: 311px; top: 472px; }

  /* front */
  .contact-list { position: absolute; left: 40px; top: 36px; color: var(--grey); font-size: 15px; line-height: 19px; }
  .contact-row { display: flex; align-items: flex-start; gap: 10px; }
  .contact-row.address { margin-bottom: 7px; }
  .contact-row svg { flex: none; width: 14px; height: 14px; margin-top: 2px; fill: var(--red); }
  .identity { position: absolute; right: 36px; top: 33px; text-align: right; }
  .person-name { font-family: "Roboto Condensed", Arial, sans-serif; font-weight: 700; font-size: 21px; color: var(--red); line-height: 24px; }
  .person-role { font-family: "Roboto Condensed", Arial, sans-serif; font-size: 15.5px; color: var(--ink); line-height: 20px; }
  .person-mobile { font-weight: 700; font-size: 18px; color: var(--grey); margin-top: 8px; line-height: 22px; }
  .person-email { font-size: 14.5px; color: var(--grey); line-height: 20px; }
  .front-art {
    position: absolute; left: 0; right: 0; top: 150px; bottom: 0;
    background: linear-gradient(110deg, var(--red-soft) 0%, #e39a9c 30%, var(--red) 65%, var(--red-dark) 100%);
  }
  .website {
    position: absolute; right: 33px; bottom: 26px;
    color: var(--white); font-weight: 700; font-size: 13px; letter-spacing: 3.6px;
  }

  /* back */
  .brand { position: absolute; left: 0; right: 0; top: 98px; display: flex; justify-content: center; align-items: center; gap: 18px; }
  .brand-square { width: 50px; height: 50px; background: var(--red); }
  .brand-name { font-weight: 700; font-size: 54px; color: var(--ink); letter-spacing: -1px; line-height: 1; }
  .service-band {
    position: absolute; left: 0; bottom: 0; width: 600px; height: 79px;
    background: linear-gradient(100deg, var(--red-dark) 0%, var(--red-soft) 35%, var(--red) 60%, #c84a4f 80%, var(--red-dark) 100%);
  }
  .services { position: absolute; left: 47px; bottom: 26px; display: flex; gap: 40px; }
  .service { display: flex; align-items: center; gap: 8px; color: var(--white); font-weight: 700; font-size: 23px; line-height: 1; }
  .service-mark { width: 18px; height: 18px; border: 3px solid var(--white); }
</style>
</head>
<body>

<section class="card card-front">
  <div class="front-art" role="img" aria-label="Red faceted abstract artwork"></div>

  <div class="contact-list">
    <div class="contact-row address">
      <svg viewBox="0 0 24 24"><path d="M12 1a8 8 0 0 0-8 8c0 6 8 14 8 14s8-8 8-14a8 8 0 0 0-8-8zm0 11a3 3 0 1 1 0-6 3 3 0 0 1 0 6z"/></svg>
      <span>Level 1, 47 Fernby Street<br>Carlow Qld 4072</span>
    </div>
    <div class="contact-row">
      <svg viewBox="0 0 24 24"><path d="M6.6 10.8a15 15 0 0 0 6.6 6.6l2.2-2.2a1 1 0 0 1 1-.3 11 11 0 0 0 3.6.6 1 1 0 0 1 1 1V20a1 1 0 0 1-1 1A17 17 0 0 1 3 4a1 1 0 0 1 1-1h3.5a1 1 0 0 1 1 1 11 11 0 0 0 .6 3.6 1 1 0 0 1-.3 1z"/></svg>
      <span>+61 (0)7 3900 4120</span>
    </div>
    <div class="contact-row">
      <svg viewBox="0 0 24 24"><path d="M6.6 10.8a15 15 0 0 0 6.6 6.6l2.2-2.2a1 1 0 0 1 1-.3 11 11 0 0 0 3.6.6 1 1 0 0 1 1 1V20a1 1 0 0 1-1 1A17 17 0 0 1 3 4a1 1 0 0 1 1-1h3.5a1 1 0 0 1 1 1 11 11 0 0 0 .6 3.6 1 1 0 0 1-.3 1z"/></svg>
      <span>+61 (0)7 3900 4137</span>
    </div>
    <div class="contact-row">
      <svg viewBox="0 0 24 24"><path d="M6 3h9l3 3v5H6zM2 12h20v8H2zm4 2v2h4v-2z"/></svg>
      <span>+61 (0)7 3900 4109</span>
    </div>
  </div>

  <div class="identity">
    <div class="person-name">MAREN HALSTEAD</div>
    <div class="person-role">Business Development Manager</div>
    <div class="person-mobile">+61 (0)455 310 628</div>
    <div class="person-email">mhalstead@korvalit.com.au</div>
  </div>

  <div class="website">www.korvalit.com.au</div>
</section>

<section class="card card-back">
  <div class="brand">
    <div class="brand-square"></div>
    <div class="brand-name">korvalIT</div>
  </div>
  <div class="service-band" role="img" aria-label="Red faceted abstract band"></div>
  <div class="services">
    <div class="service"><span class="service-mark"></span>MapOut</div>
    <div class="service"><span class="service-mark"></span>ShipWell</div>
    <div class="service"><span class="service-mark"></span>KeepSteady</div>
  </div>
</section>

</body>
</html>
```